Business Card Design Project

We are a construction company in Orange County, CA. We need a two sided business card. We would like the back to be our logo with web URL. Front should included Name, title, address, phone, fax and email address.

our address is
627 West Dorrance Blvd, Suite 308
Anaheim, CA 92718

Our logo files are attached.

Construction

```html
<!DOCTYPE html>
<html lang="en">
<head>
<meta charset="utf-8">
<title>Kestra Business Card</title>
<link rel="stylesheet" href="https://fonts.googleapis.com/css2?family=Open+Sans:wght@400;600;700&display=swap">
<style>
  :root {
    --brand-blue: #164a7e;
    --swoosh-grey: #9a9a9a;
    --card-white: #ffffff;
    --ink-grey: #666666;
    --backdrop: #eceae6;
    --on-blue: #ffffff;
  }
  * { margin: 0; padding: 0; box-sizing: border-box; }
  html, body {
    width: 1200px; height: 444px; overflow: hidden;
    background: var(--backdrop);
    font-family: "Open Sans", Arial, sans-serif;
  }
  .canvas { position: relative; width: 1200px; height: 444px; }
  .card {
    position: absolute; top: 75px; width: 516px; height: 295px;
    background: var(--card-white); border-radius: 12px; overflow: hidden;
    box-shadow: 0 2px 6px rgba(0,0,0,0.25);
  }
  .card--front { left: 72px; }
  .card--back { left: 612px; }
  .wordmark {
    position: absolute; left: 0; right: 0; text-align: center;
    color: var(--brand-blue); font-weight: 700; letter-spacing: 1px; line-height: 1;
  }
  .card--front .wordmark { top: 74px; font-size: 54px; }
  .card--back .wordmark { top: 116px; font-size: 54px; }
  .identity {
    position: absolute; top: 160px; left: 0; right: 0;
    display: flex; justify-content: center; align-items: center;
  }
  .identity__name { color: var(--brand-blue); font-weight: 700; font-size: 17px; padding-right: 8px; }
  .identity__title { color: var(--ink-grey); font-size: 14px; padding-left: 8px; border-left: 1px solid var(--ink-grey); line-height: 22px; }
  .wave { position: absolute; left: 0; top: 0; width: 516px; height: 295px; }
  .contact {
    position: absolute; left: 0; right: 0; top: 240px;
    display: flex; justify-content: center; gap: 10px;
    color: var(--on-blue); font-size: 13px;
  }
  .contact__item { display: flex; align-items: center; gap: 3px; }
  .contact__item svg { width: 11px; height: 11px; fill: var(--on-blue); }
  .address { position: absolute; left: 0; right: 0; top: 264px; text-align: center; color: var(--on-blue); font-size: 13px; }
  .web-address {
    position: absolute; left: 0; right: 0; top: 222px; text-align: center;
    color: var(--ink-grey); font-size: 13px; letter-spacing: 3px;
  }
</style>
</head>
<body>
<div class="canvas">
  <section class="card card--front">
    <svg class="wave" viewBox="0 0 516 295" aria-hidden="true">
      <path d="M0 180 C120 175 200 215 300 205 C390 196 450 200 516 222 L516 230 C450 210 390 206 300 216 C200 226 110 196 0 196 Z" fill="var(--swoosh-grey)"/>
      <path d="M0 196 C110 196 200 226 300 216 C390 206 450 212 516 230 L516 295 L0 295 Z" fill="var(--brand-blue)"/>
    </svg>
    <div class="wordmark">KESTRA</div>
    <div class="identity">
      <span class="identity__name">YOUR NAME</span>
      <span class="identity__title">Title</span>
    </div>
    <div class="contact">
      <span class="contact__item"><svg viewBox="0 0 12 12"><path d="M2.5 1 L4.5 1 L5.3 3.5 L4 4.6 C4.6 6 5.9 7.3 7.4 8 L8.5 6.7 L11 7.5 L11 9.5 C11 10.3 10.3 11 9.5 11 C5 11 1 7 1 2.5 C1 1.7 1.7 1 2.5 1 Z"/></svg>0123456789</span>
      <span class="contact__item"><svg viewBox="0 0 12 12"><path d="M3 1 H8 V4 H3 Z M1 5 H11 V10 H1 Z M3 7 H9 V8 H3 Z"/></svg>0123456789</span>
      <span class="contact__item"><svg viewBox="0 0 12 12"><path d="M1 3 H11 V10 H1 Z M1.5 3.5 L6 7 L10.5 3.5 V4.5 L6 8 L1.5 4.5 Z" fill-rule="evenodd"/></svg>info@kestrabuild.com</span>
      <span class="contact__item"><svg viewBox="0 0 12 12"><path d="M6 1 A5 5 0 1 0 6.01 1 Z M6 2 A4 4 0 1 1 5.99 2 Z M5.5 1.5 H6.5 V10.5 H5.5 Z M1.5 5.5 H10.5 V6.5 H1.5 Z" fill-rule="evenodd"/></svg>www.kestrabuild.com</span>
    </div>
    <div class="address">627 West Dorrance Blvd, Suite 308 Anaheim, CA 92718</div>
  </section>

  <section class="card card--back">
    <div class="wordmark">KESTRA</div>
    <div class="web-address">www.kestrabuild.com</div>
  </section>
</div>
</body>
</html>
```